Elegant, Playful ReDesign of Paperlynx Website in wordpress - Budget has been raised

Project Brief: Paperlynx Website Redesign in WordPress

Introduction: Paperlynx, a cutting-edge document creation solution, aims to revolutionize the tedious process of crafting contracts, offers, forms, and other documents. By saving customers valuable time, streamlining workflows, and minimizing human error, Paperlynx has become an essential tool. As a technology company with a diverse clientele, we're set to boost our online presence through a refreshed WordPress website. Beyond a modernized website, we aspire to establish a stronger brand identity, incorporating graphic elements seamlessly into our online presence.

Current Status: Currently hosted on WordPress, Paperlynx's existing website serves its purpose but is ready for a visual transformation. Our goal is to maintain a modern and attractive appearance while upholding our commitment to simplicity and efficiency. Notably, the website is currently only in Danish. The redesigned structure should include a language switch function to cater to future international customers.

Objectives:
• Modern Aesthetic: Redesign the website with a fresh and modern vibe, reflecting innovation in the document creation sphere.
• User-Friendly: Prioritize an intuitive design for seamless navigation, ensuring visitors easily understand our offerings and benefits.
• Informative Content: Strike a balance between attractiveness and informativeness, clearly communicating Paperlynx's value proposition and simplifying business processes.
• Graphic Elements: Integrate visually appealing graphics that enhance the site's aesthetics and contribute to our overall visual identity. These elements should be versatile for future use in social media, advertisements, and other branding materials.
• Brand Recognition: Maintain our current logo and color scheme while exploring creative ways to establish a distinctive brand identity. The website should be a cornerstone for a cohesive branding strategy.
• Media Integration: Include images or videos on the website to enhance engagement. Find suitable, free-to-use visuals.
• Responsiveness: Ensure the design is responsive and works seamlessly on all devices.
• Demo Booking Form: Improve the design of the form to book a demo.
• Multilingual Support: Enable language transformation; the website is currently in Danish but should cater to other countries.

Guidelines:
• Typography: Up to the designer's discretion.
• Images/Videos: Must be free to use without additional charges.
• WordPress Theme: Use any WordPress theme below $100.
• Logo Redesign: Not needed; stick to the referenced color palette, as our new logo uses these colors.
• Color Palette: Stick to the existing company colors for consistency:
RGB
• #000b3c
• #004c6c
• #319ac3
• Greytones and white are also allowed
• Creativity Encouraged: Embrace creativity within the color palette for the layout, visuals, and overall user experience.

Conclusion: The Paperlynx website redesign marks an exciting opportunity to enhance our online presence. Our goal is to achieve a balance between a modern, attractive design and a clear, informative representation of our innovative solutions. We envision the revamped website as the foundation for a compelling online brand presence, with versatile graphic elements resonating across various digital platforms.

Sections that the website must include: Space for customer logos, space for testimonials, Space and redesign for display of price structure and price comparison, sections for company details and other information.

Design should also include a redesign of the customer cases section.
Generally there should just be a redesign of all things that are on the website.

Link to current website: https://paperlynx.example/

Target Market(s)

+50 employees.

Industry/Entity Type

Document automation

Coding

Coded - Design and coding required

Number of Pages Required

5+ page

Colors
0054AA
0677BA
7BADD7
CADEEF
E8F1F8

Requirements
Must have
• The new webpage must have the same pages as the current one. Frontpage, Book demo, About us, Case stories and Pricing

```html
<!DOCTYPE html>
<html lang="en">
<head>
<meta charset="utf-8">
<title>Paperlynx – Create error-free contracts and quotes quickly</title>
<link href="https://fonts.googleapis.com/css2?family=Archivo:wght@500;600;700&family=Poppins:wght@400;500;600&display=swap" rel="stylesheet">
<style>
:root{
  --navy:#0c2340;
  --navy-deep:#0a1c36;
  --teal:#0e5f7e;
  --blue:#1c98d3;
  --blue-bright:#1ea3dc;
  --ink:#1d1d1f;
  --text:#555b63;
  --grey-bg:#f1f2f3;
  --line:#e3e6ea;
  --white:#ffffff;
}
*{margin:0;padding:0;box-sizing:border-box}
html,body{width:1200px;height:5155px;overflow:hidden}
body{font-family:"Poppins",sans-serif;color:var(--text);background:var(--white);position:relative}
.abs{position:absolute}
h1,h2,h3,h4{font-family:"Archivo",sans-serif;color:var(--ink)}
.btn{position:absolute;display:flex;align-items:center;justify-content:center;gap:10px;border-radius:30px;color:var(--white);font-size:14px;font-weight:500;letter-spacing:.2px;text-decoration:none}
.btn .arr{width:22px;height:22px;border-radius:50%;background:var(--white);display:flex;align-items:center;justify-content:center}
.btn-blue{background:var(--blue)}

/* header */
.site-header{position:absolute;left:0;top:0;width:1200px;height:140px;background:var(--white)}
.brand{position:absolute;display:flex;align-items:center;gap:12px}
.brand .mark{width:34px;height:34px;background:var(--blue)}
.brand .name{font-family:"Archivo",sans-serif;font-weight:700;font-size:34px;color:var(--navy);letter-spacing:.5px}
.phone-pill{position:absolute;left:766px;top:36px;width:164px;height:36px;border:2px solid var(--navy);border-radius:20px;display:flex;align-items:center;font-size:13px;color:var(--navy);font-weight:500}
.phone-pill .ico{width:32px;height:32px;border-radius:50%;background:var(--navy);margin-right:12px;display:flex;align-items:center;justify-content:center}
.book-pill{left:950px;top:36px;width:164px;height:36px;font-size:13px}
.nav{position:absolute;top:92px;right:86px;display:flex;gap:48px;font-size:13px;color:var(--ink)}
.nav .active{color:var(--blue)}

/* hero */
.hero{position:absolute;left:0;top:140px;width:1200px;height:636px;background:var(--navy-deep)}
.hero .side{position:absolute;left:856px;top:0;width:344px;height:636px;background:var(--blue)}
.hero h1{position:absolute;left:88px;top:104px;width:620px;color:var(--white);font-size:43px;line-height:51px;font-weight:700}
.checks{position:absolute;left:88px;top:288px;list-style:none}
.checks li{display:flex;align-items:center;gap:14px;height:44px;color:var(--white);font-size:17px}
.checks .tick{width:30px;height:30px;border:2px solid var(--blue);border-radius:50%;display:flex;align-items:center;justify-content:center}
.hero .btn{left:88px;top:496px;width:194px;height:58px;font-size:15px}
.hero-visual{position:absolute;left:654px;top:134px;width:440px;height:440px}

/* features */
.features{position:absolute;left:0;top:776px;width:1200px;height:410px}
.feature{position:absolute;top:68px;width:300px;text-align:center}
.feature .icon{margin:0 auto;width:122px;height:112px;position:relative}
.feature h3{margin-top:26px;font-size:19px;letter-spacing:.3px;font-weight:600}
.feature p{margin:18px auto 0;width:250px;font-size:14.5px;line-height:26px}

/* about */
.about{position:absolute;left:0;top:1186px;width:1200px;height:614px;background:var(--grey-bg)}
.section-title{display:flex;align-items:center;gap:12px;font-family:"Archivo",sans-serif;font-weight:700;color:var(--ink);letter-spacing:.3px}
.section-title .mark{background:var(--blue)}
.section-title em{font-style:normal;color:var(--blue)}
.about .section-title{position:absolute;left:632px;top:138px;font-size:31px}
.about .section-title .mark{width:26px;height:26px}
.about p{position:absolute;left:632px;top:200px;width:432px;font-size:14.5px;line-height:31px;text-align:justify}
.about .btn{left:632px;top:420px;width:154px;height:46px;font-size:13px}

/* intelligent solution */
.solution{position:absolute;left:0;top:1800px;width:1200px;height:780px}
.solution .section-title{position:absolute;left:0;top:96px;width:1200px;justify-content:center;font-size:40px}
.solution .section-title .mark{width:46px;height:46px}
.lead{position:absolute;font-size:14.5px;line-height:26px;text-align:center;color:#3d4249}
.solution .lead{left:90px;top:192px;width:1020px}
.step-label{position:absolute;font-family:"Archivo",sans-serif;font-weight:600;font-size:22px;color:var(--ink);transform:translateX(-50%);white-space:nowrap}
.step-num{position:absolute;font-family:"Archivo",sans-serif;font-weight:700;font-size:56px;color:var(--ink);transform:translateX(-50%)}
.shot{position:absolute;background:var(--white);box-shadow:0 4px 14px rgba(0,0,0,.14);padding:18px 22px}

/* live demo */
.live-demo{position:absolute;left:0;top:2580px;width:1200px;height:470px;background:linear-gradient(100deg,#163a62 0%,#1d4a78 45%,#15385f 100%)}
.live-demo .section-title{position:absolute;left:0;top:106px;width:1200px;justify-content:center;font-size:40px;color:var(--white)}
.live-demo .section-title .mark{width:46px;height:46px;background:var(--white)}
.live-demo .lead{left:200px;top:196px;width:800px;color:var(--white);line-height:31px}
.live-demo .btn{left:464px;top:302px;width:272px;height:68px;font-size:16px}

/* integration */
.integration{position:absolute;left:0;top:3050px;width:1200px;height:870px}
.integration .section-title{position:absolute;left:0;top:106px;width:1200px;justify-content:center;font-size:40px}
.integration .section-title .mark{width:46px;height:46px}
.integration .lead{left:140px;top:190px;width:920px}
.integration .lead b{color:var(--navy);font-weight:600;text-decoration:underline}
.int-card{position:absolute;top:310px;width:328px;height:440px;background:var(--white);box-shadow:0 3px 14px rgba(0,0,0,.12);text-align:center}
.int-card .circle{width:124px;height:124px;border-radius:50%;margin:46px auto 0;display:flex;align-items:center;justify-content:center}
.int-card h3{margin-top:36px;font-size:18px;font-weight:600;letter-spacing:.3px}
.int-card p{margin:22px auto 0;width:270px;font-size:14px;line-height:26px}
.int-card .btn{left:87px;top:360px;width:154px;height:42px;font-size:13px}

/* testimonials */
.testimonials{position:absolute;left:0;top:3920px;width:1200px;height:610px;background:#f5f6f7}
.testimonials .section-title{position:absolute;left:0;top:100px;width:1200px;justify-content:center;font-size:40px}
.testimonials .section-title .mark{width:46px;height:46px}
.quote-card{position:absolute;top:204px;width:244px;height:376px;background:var(--white);box-shadow:0 2px 10px rgba(0,0,0,.08);text-align:center;padding:0 22px}
.quote-card .mark{width:36px;height:36px;background:var(--blue);margin:46px auto 0}
.quote-card p{margin-top:26px;font-size:12.5px;line-height:22px;color:#3d4249}
.person{position:absolute;left:36px;top:248px;display:flex;align-items:center;gap:14px;text-align:left}
.person .avatar{width:44px;height:44px;border-radius:50%;background:linear-gradient(135deg,#c9a98d,#8e6d56)}
.person .who{font-size:12px;font-weight:600;color:var(--ink);line-height:16px}

/* client logos */
.clients{position:absolute;left:0;top:4530px;width:1200px;height:190px;background:var(--white)}
.clients .row{position:absolute;left:160px;top:84px;width:880px;display:flex;justify-content:space-between;align-items:center}
.client{display:flex;align-items:center;gap:8px;font-family:"Archivo",sans-serif;font-weight:600;font-size:21px;color:#3a3d42}
.client .sq{width:18px;height:18px;background:#3a3d42}
.clients .chev{position:absolute;top:86px}

/* footer */
.site-footer{position:absolute;left:0;top:4720px;width:1200px;height:372px;background:var(--navy-deep)}
.site-footer .brand .name{color:var(--white);font-size:30px}
.site-footer .brand .mark{background:var(--white)}
.col-title{position:absolute;font-family:"Archivo",sans-serif;font-weight:600;font-size:19px;color:var(--blue)}
.col-title::after{content:"";position:absolute;left:0;top:32px;width:40px;height:2px;background:var(--blue)}
.links{position:absolute;left:426px;top:142px;list-style:none}
.links li{display:flex;align-items:center;gap:18px;height:31px;font-size:14px;color:var(--white)}
.links .sq{width:18px;height:18px;background:var(--white)}
.contact-item{position:absolute;left:646px;display:flex;gap:22px;align-items:flex-start;color:var(--white);font-size:13.5px;line-height:18px}
.contact-item .box,.social .box{width:30px;height:30px;border:1.5px solid var(--white);border-radius:5px;display:flex;align-items:center;justify-content:center;flex-shrink:0}
.social{position:absolute;left:962px;display:flex;align-items:center;gap:20px;color:var(--white);font-size:14px}
.social .box .dot{width:12px;height:12px;background:var(--white)}
.legal-bar{position:absolute;left:0;top:5092px;width:1200px;height:63px;background:var(--blue);color:var(--white);font-size:12.5px}
.legal-bar .l{position:absolute;left:90px;top:22px}
.legal-bar .r{position:absolute;right:84px;top:22px}
</style>
</head>
<body>

<header class="site-header">
  <div class="brand" style="left:90px;top:52px">
    <span class="mark"></span><span class="name">PAPERLYNX</span>
  </div>
  <div class="phone-pill"><span class="ico"><svg width="16" height="16" viewBox="0 0 24 24"><path d="M6.6 10.8a15 15 0 0 0 6.6 6.6l2.2-2.2c.3-.3.7-.4 1-.2 1.1.4 2.3.6 3.6.6.6 0 1 .4 1 1V20c0 .6-.4 1-1 1A17 17 0 0 1 3 4c0-.6.4-1 1-1h3.5c.6 0 1 .4 1 1 0 1.3.2 2.5.6 3.6.1.3 0 .7-.2 1z" fill="#fff"/></svg></span>555-010-1200</div>
  <a class="btn btn-blue book-pill">BOOK DEMO</a>
  <nav class="nav"><span class="active">HOME</span><span>CUSTOMER CASES</span><span>VIDEO</span><span>LIVE DEMO</span><span>PRICES</span><span>ABOUT US</span></nav>
</header>

<section class="hero">
  <div class="side"></div>
  <h1>CREATE ERROR-FREE CONTRACTS AND QUOTES QUICKLY</h1>
  <ul class="checks">
    <li><span class="tick"><svg width="14" height="14" viewBox="0 0 14 14"><path d="M2 7.5l3 3 7-7" stroke="#fff" stroke-width="2" fill="none"/></svg></span>Get paragraphs inserted automatically</li>
    <li><span class="tick"><svg width="14" height="14" viewBox="0 0 14 14"><path d="M2 7.5l3 3 7-7" stroke="#fff" stroke-width="2" fill="none"/></svg></span>Get prices calculated automatically</li>
    <li><span class="tick"><svg width="14" height="14" viewBox="0 0 14 14"><path d="M2 7.5l3 3 7-7" stroke="#fff" stroke-width="2" fill="none"/></svg></span>Eliminate manual work</li>
    <li><span class="tick"><svg width="14" height="14" viewBox="0 0 14 14"><path d="M2 7.5l3 3 7-7" stroke="#fff" stroke-width="2" fill="none"/></svg></span>Sign digitally</li>
  </ul>
  <a class="btn btn-blue">GOT STARTED <span class="arr"><svg width="10" height="10" viewBox="0 0 10 10"><path d="M3 1l4 4-4 4" stroke="#0c2340" stroke-width="2" fill="none"/></svg></span></a>
  <svg class="hero-visual" viewBox="0 0 440 440">
    <defs><linearGradient id="heroImg" x1="0" y1="0" x2="1" y2="1"><stop offset="0" stop-color="#e8edf3"/><stop offset=".6" stop-color="#b9c7d6"/><stop offset="1" stop-color="#7f95ad"/></linearGradient></defs>
    <circle cx="220" cy="220" r="214" fill="none" stroke="#fff" stroke-width="5"/>
    <circle cx="220" cy="220" r="190" fill="url(#heroImg)" role="img" aria-label="Hand working on charts and documents beside a globe icon"/>
  </svg>
</section>

<section class="features">
  <div class="feature" style="left:146px">
    <div class="icon"><svg width="122" height="112" viewBox="0 0 122 112"><rect x="0" y="0" width="9" height="112" fill="#0c2340"/><rect x="14" y="0" width="9" height="112" fill="#0c2340"/><rect x="28" y="0" width="94" height="112" fill="#1c98d3"/><path d="M63 38h22M63 76h22M66 38c0 12 16 14 16 19s-16 7-16 19M82 38c0 12-16 14-16 19s16 7 16 19" stroke="#fff" stroke-width="3" fill="none"/></svg></div>
    <h3>SAVE TIME</h3>
    <p>Reduce your time consumption by up to 90% when creating customer contracts and offers.</p>
  </div>
  <div class="feature" style="left:448px">
    <div class="icon"><svg width="122" height="112" viewBox="0 0 122 112"><rect x="0" y="0" width="9" height="112" fill="#0c2340"/><rect x="14" y="0" width="9" height="112" fill="#0c2340"/><rect x="28" y="0" width="94" height="112" fill="#1c98d3"/><path d="M75 38l16 6v12c0 10-7 16-16 20-9-4-16-10-16-20V44z" fill="#fff"/><path d="M68 56l5 5 9-10" stroke="#1c98d3" stroke-width="3" fill="none"/></svg></div>
    <h3>HIGH QUALITY</h3>
    <p>Automation gives you minimal work and eliminates errors in your documents.</p>
  </div>
  <div class="feature" style="left:750px">
    <div class="icon"><svg width="122" height="112" viewBox="0 0 122 112"><rect x="0" y="0" width="9" height="112" fill="#0c2340"/><rect x="14" y="0" width="9" height="112" fill="#0c2340"/><rect x="28" y="0" width="94" height="112" fill="#1c98d3"/><path d="M64 68l10-20 14 12M74 48l14-6" stroke="#fff" stroke-width="2.5" fill="none"/><circle cx="64" cy="68" r="5" fill="#fff"/><circle cx="74" cy="48" r="5" fill="#fff"/><circle cx="88" cy="60" r="5" fill="#fff"/><circle cx="88" cy="42" r="4" fill="#fff"/></svg></div>
    <h3>STREAMLINED FLOW</h3>
    <p>Be guided all the way through the document and ask for review before sending the document for digital signature.</p>
  </div>
</section>

<section class="about">
  <svg class="abs" style="left:130px;top:86px" width="452" height="452" viewBox="0 0 452 452">
    <defs><linearGradient id="aboutImg" x1="0" y1="0" x2="1" y2="1"><stop offset="0" stop-color="#d8d4c8"/><stop offset=".5" stop-color="#eceae4"/><stop offset="1" stop-color="#9aa2a8"/></linearGradient></defs>
    <circle cx="226" cy="226" r="223" fill="none" stroke="#1c98d3" stroke-width="3"/>
    <circle cx="226" cy="226" r="200" fill="url(#aboutImg)" role="img" aria-label="Laptop on a desk with folders, books and flowers"/>
  </svg>
  <h2 class="section-title"><span class="mark"></span>ABOUT <em>US</em></h2>
  <p>Paperlynx started with a desire to make it easy and cheap to create legal documents. It was difficult to compare prices and the existing templates were difficult to fill out. Paperlynx's founder Henrik Vestergaard tried the difficult process on his own, and saw an opportunity in making it streamlined and digital.</p>
  <a class="btn btn-blue">READ MORE <span class="arr"><svg width="10" height="10" viewBox="0 0 10 10"><path d="M3 1l4 4-4 4" stroke="#0c2340" stroke-width="2" fill="none"/></svg></span></a>
</section>

<section class="solution">
  <h2 class="section-title"><span class="mark"></span>INTELLIGENT <em>DOCUMENT SOLUTION</em></h2>
  <p class="lead">Leave the creation of your documents to our intelligent solution. It can automatically calculate your prices and insert the sections that need to be included in your documents. Get rid of manual work with legal uncertainties and become more efficient.</p>
  <svg class="abs" style="left:0;top:0" width="1200" height="780" viewBox="0 0 1200 780">
    <path d="M108 496V642H434V344H764V642H1090V496" fill="none" stroke="#1c98d3" stroke-width="2.5"/>
    <circle cx="108" cy="496" r="6" fill="#0c2340"/><circle cx="434" cy="496" r="6" fill="#0c2340"/>
    <circle cx="764" cy="496" r="6" fill="#0c2340"/><circle cx="1090" cy="496" r="6" fill="#0c2340"/>
  </svg>
  <span class="step-label" style="left:270px;top:326px">Select Document</span>
  <span class="step-num" style="left:602px;top:256px">2</span>
  <span class="step-label" style="left:930px;top:326px">Sign digitally</span>
  <span class="step-label" style="left:600px;top:632px">Complete guided flow</span>
  <span class="step-num" style="left:274px;top:650px">1</span>
  <span class="step-num" style="left:930px;top:650px">3</span>

  <div class="shot" style="left:146px;top:378px;width:252px;height:232px">
    <svg width="208" height="196" viewBox="0 0 208 196">
      <text x="8" y="12" font-size="9" fill="#555" font-family="Poppins,sans-serif">Employment (HR)</text>
      <line x1="8" y1="22" x2="200" y2="22" stroke="#d0d4d9"/>
      <g fill="#c5cad0"><rect x="8" y="30" width="60" height="3"/><rect x="8" y="40" width="54" height="3"/><rect x="8" y="50" width="64" height="3"/><rect x="8" y="60" width="50" height="3"/><rect x="8" y="70" width="58" height="3"/><rect x="8" y="80" width="62" height="3"/><rect x="8" y="90" width="48" height="3"/><rect x="8" y="100" width="70" height="3"/><rect x="8" y="110" width="52" height="3"/></g>
      <g fill="#6b7079"><rect x="184" y="29" width="5" height="5"/><rect x="184" y="39" width="5" height="5"/><rect x="184" y="49" width="5" height="5"/><rect x="184" y="59" width="5" height="5"/><rect x="184" y="69" width="5" height="5"/><rect x="184" y="79" width="5" height="5"/><rect x="184" y="89" width="5" height="5"/><rect x="184" y="99" width="5" height="5"/><rect x="184" y="109" width="5" height="5"/></g>
      <text x="8" y="138" font-size="9" fill="#555" font-family="Poppins,sans-serif">Sales</text>
      <line x1="8" y1="146" x2="200" y2="146" stroke="#d0d4d9"/>
      <g fill="#c5cad0"><rect x="8" y="154" width="44" height="3"/><rect x="8" y="164" width="56" height="3"/><rect x="8" y="174" width="62" height="3"/><rect x="8" y="184" width="50" height="3"/></g>
      <g fill="#6b7079"><rect x="184" y="153" width="5" height="5"/><rect x="184" y="163" width="5" height="5"/><rect x="184" y="173" width="5" height="5"/><rect x="184" y="183" width="5" height="5"/></g>
    </svg>
  </div>
  <div class="shot" style="left:472px;top:378px;width:252px;height:206px">
    <svg width="208" height="170" viewBox="0 0 208 170">
      <rect x="4" y="8" width="50" height="4" fill="#555"/>
      <rect x="4" y="18" width="196" height="3" fill="#c5cad0"/><rect x="4" y="24" width="160" height="3" fill="#c5cad0"/>
      <rect x="4" y="32" width="140" height="10" fill="none" stroke="#7cc08d"/>
      <rect x="4" y="46" width="10" height="6" fill="none" stroke="#aaa"/><rect x="18" y="48" width="40" height="3" fill="#c5cad0"/>
      <rect x="4" y="66" width="48" height="4" fill="#555"/>
      <g fill="#c5cad0"><rect x="4" y="78" width="36" height="3"/><rect x="4" y="90" width="64" height="3"/><rect x="4" y="104" width="34" height="3"/><rect x="4" y="116" width="28" height="3"/><rect x="60" y="116" width="28" height="3"/><rect x="4" y="132" width="56" height="3"/></g>
      <g stroke="#d0d4d9"><line x1="4" y1="96" x2="200" y2="96"/><line x1="4" y1="122" x2="200" y2="122"/><line x1="4" y1="138" x2="200" y2="138"/></g>
    </svg>
  </div>
  <div class="shot" style="left:800px;top:378px;width:254px;height:232px;padding:14px">
    <svg width="226" height="204" viewBox="0 0 226 204">
      <rect x="0" y="0" width="226" height="10" fill="#2f3640"/>
      <rect x="0" y="10" width="8" height="194" fill="#3a3f47"/><rect x="208" y="10" width="18" height="194" fill="#3a3f47"/>
      <rect x="18" y="20" width="182" height="150" fill="#fff" stroke="#e1e3e6"/>
      <rect x="32" y="82" width="44" height="3" fill="#555"/><rect x="32" y="90" width="36" height="2" fill="#b5bac0"/><rect x="32" y="96" width="30" height="2" fill="#b5bac0"/>
      <rect x="160" y="82" width="20" height="2" fill="#b5bac0"/>
      <rect x="26" y="176" width="170" height="18" fill="#2f3640"/><rect x="176" y="181" width="18" height="8" fill="#4cba6b"/>
      <rect x="212" y="90" width="6" height="26" fill="#4cba6b"/>
    </svg>
  </div>
</section>

<section class="live-demo" role="img" aria-label="Dark blue background photo of a person creating documents on a laptop">
  <h2 class="section-title"><span class="mark"></span>START LIVE DEMO</h2>
  <p class="lead">Experience the intuitive and intelligent flow of creating documents on your own. In a few minutes you have a complete document – ready for digital signature.</p>
  <a class="btn btn-blue">START LIVE DEMO <span class="arr"><svg width="10" height="10" viewBox="0 0 10 10"><path d="M3 1l4 4-4 4" stroke="#0c2340" stroke-width="2" fill="none"/></svg></span></a>
</section>

<section class="integration">
  <h2 class="section-title"><span class="mark"></span>INTEGRATION <em>TO CRM</em></h2>
  <p class="lead">Create your offers or customer contracts directly in your CRM solution, and send them for digital signature with a few clicks. Experience better insight and timing in your sales with an integration to <b>Salesdesk</b> . The integration has been created in collaboration with <b>Webmill</b> .</p>
  <div class="int-card" style="left:88px">
    <div class="circle" style="background:var(--navy)"><svg width="60" height="52" viewBox="0 0 60 52"><rect x="4" y="10" width="44" height="34" fill="none" stroke="#fff" stroke-width="2.5"/><path d="M12 34c6-10 10 6 16-4s8 2 12-2" stroke="#fff" stroke-width="2" fill="none"/><path d="M42 32L56 6" stroke="#fff" stroke-width="3"/></svg></div>
    <h3>DIGITAL SIGNATURE</h3>
    <p>Digital signature Send your offers for digital signature with data directly from your CRM solution - quickly and easily.</p>
    <a class="btn" style="background:var(--navy)">READ MORE <span class="arr"><svg width="10" height="10" viewBox="0 0 10 10"><path d="M3 1l4 4-4 4" stroke="#0c2340" stroke-width="2" fill="none"/></svg></span></a>
  </div>
  <div class="int-card" style="left:440px">
    <div class="circle" style="background:var(--teal)"><svg width="60" height="56" viewBox="0 0 60 56"><circle cx="34" cy="20" r="14" fill="none" stroke="#fff" stroke-width="2.5"/><path d="M28 26l12-12" stroke="#fff" stroke-width="2.5"/><circle cx="29" cy="16" r="2.5" fill="#fff"/><circle cx="39" cy="25" r="2.5" fill="#fff"/><path d="M4 44h12l10 4h16l12-8" stroke="#fff" stroke-width="2.5" fill="none"/></svg></div>
    <h3>AUTOMATED OFFERS</h3>
    <p>Create error-free offers with data from your CRM solution using a guided flow and avoid manual errors.</p>
    <a class="btn" style="background:var(--teal)">READ MORE <span class="arr"><svg width="10" height="10" viewBox="0 0 10 10"><path d="M3 1l4 4-4 4" stroke="#0c2340" stroke-width="2" fill="none"/></svg></span></a>
  </div>
  <div class="int-card" style="left:790px">
    <div class="circle" style="background:var(--blue-bright)"><svg width="62" height="54" viewBox="0 0 62 54"><rect x="4" y="4" width="50" height="38" rx="4" fill="none" stroke="#fff" stroke-width="2.5"/><line x1="4" y1="14" x2="54" y2="14" stroke="#fff" stroke-width="2"/><path d="M20 22l-6 6 6 6M32 22l6 6-6 6" stroke="#fff" stroke-width="2.5" fill="none"/><circle cx="48" cy="40" r="9" fill="#1ea3dc" stroke="#fff" stroke-width="2.5"/></svg></div>
    <h3>LEADS FROM YOUR WEBSITE</h3>
    <p>Manage your leads and customer inquiries with intelligent forms directly on your own website.</p>
    <a class="btn" style="background:var(--blue-bright)">READ MORE <span class="arr"><svg width="10" height="10" viewBox="0 0 10 10"><path d="M3 1l4 4-4 4" stroke="#0c2340" stroke-width="2" fill="none"/></svg></span></a>
  </div>
</section>

<section class="testimonials">
  <h2 class="section-title"><span class="mark"></span>APPRECIATED AND <em>RECOMMENDED BY</em></h2>
  <div class="quote-card" style="left:78px">
    <div class="mark"></div>
    <p>I didn't imagine our offer could be fully automated just like that, but we gave it a shot because I saw what others had done with Paperlynx.</p>
    <div class="person"><span class="avatar" role="img" aria-label="Portrait photo"></span><span class="who">Mikkel Holm<br>Sørensen</span></div>
  </div>
  <div class="quote-card" style="left:344px">
    <div class="mark"></div>
    <p>Paperlynx's solution, combined with Paperlynx's advantageous business model, is undoubtedly the best solution we have come across.</p>
    <div class="person"><span class="avatar" role="img" aria-label="Portrait photo"></span><span class="who">Jens P. Larsen</span></div>
  </div>
  <div class="quote-card" style="left:610px">
    <div class="mark"></div>
    <p>We had been looking for a long time for the right platform to digitize our unique paradigm collection, and had no doubts after being shown</p>
    <div class="person"><span class="avatar" role="img" aria-label="Portrait photo"></span><span class="who">Rasmus Bak Nielsen</span></div>
  </div>
  <div class="quote-card" style="left:878px">
    <div class="mark"></div>
    <p>Paperlynx is a really good collaboration partner within digital processes.</p>
    <div class="person"><span class="avatar" role="img" aria-label="Portrait photo"></span><span class="who">Lise Thornberg</span></div>
  </div>
</section>

<section class="clients">
  <svg class="chev" style="left:86px" width="16" height="26" viewBox="0 0 16 26"><path d="M13 2L3 13l10 11" stroke="#222" stroke-width="3" fill="none"/></svg>
  <div class="row">
    <span class="client"><span class="sq"></span>Northbay</span>
    <span class="client"><span class="sq"></span>Lexhaven</span>
    <span class="client"><span class="sq"></span>Corrupak</span>
    <span class="client"><span class="sq"></span>Webmill</span>
    <span class="client"><span class="sq"></span>Bramblefox</span>
  </div>
  <svg class="chev" style="left:1100px" width="16" height="26" viewBox="0 0 16 26"><path d="M3 2l10 11L3 24" stroke="#222" stroke-width="3" fill="none"/></svg>
</section>

<footer class="site-footer">
  <div class="brand" style="left:110px;top:172px">
    <span class="mark"></span><span class="name">PAPERLYNX</span>
  </div>
  <h4 class="col-title" style="left:426px;top:64px">Quick Links</h4>
  <ul class="links">
    <li><span class="sq"></span>Customer cases</li>
    <li><span class="sq"></span>Video</li>
    <li><span class="sq"></span>Live demo</li>
    <li><span class="sq"></span>Prices</li>
    <li><span class="sq"></span>About us</li>
    <li><span class="sq"></span>Book demo</li>
  </ul>
  <h4 class="col-title" style="left:646px;top:64px">Contact Us</h4>
  <div class="contact-item" style="top:146px"><span class="box"><svg width="14" height="14" viewBox="0 0 24 24"><path d="M6.6 10.8a15 15 0 0 0 6.6 6.6l2.2-2.2c.3-.3.7-.4 1-.2 1.1.4 2.3.6 3.6.6.6 0 1 .4 1 1V20c0 .6-.4 1-1 1A17 17 0 0 1 3 4c0-.6.4-1 1-1h3.5c.6 0 1 .4 1 1 0 1.3.2 2.5.6 3.6.1.3 0 .7-.2 1z" fill="#fff"/></svg></span><span>CALL US<br>+45 00 00 12 82</span></div>
  <div class="contact-item" style="top:202px"><span class="box"><svg width="16" height="12" viewBox="0 0 16 12"><rect x="1" y="1" width="14" height="10" fill="none" stroke="#fff" stroke-width="1.5"/><path d="M1 1l7 6 7-6" stroke="#fff" stroke-width="1.5" fill="none"/></svg></span><span>EMAIL US<br>contact@paperlynx.example</span></div>
  <div class="contact-item" style="top:258px"><span class="box"><svg width="12" height="16" viewBox="0 0 12 16"><path d="M6 15S1 9 1 6a5 5 0 0 1 10 0c0 3-5 9-5 9z" fill="#fff"/><circle cx="6" cy="6" r="2" fill="#0a1c36"/></svg></span><span>Egevej 41, 2750<br>Nordby</span></div>
  <h4 class="col-title" style="left:962px;top:64px">Follow Us</h4>
  <div class="social" style="top:150px"><span class="box"><span class="dot"></span></span>FRIENDBOOK</div>
  <div class="social" style="top:202px"><span class="box"><span class="dot"></span></span>CHIRPER</div>
  <div class="social" style="top:254px"><span class="box"><span class="dot"></span></span>LINKWORK</div>
</footer>

<div class="legal-bar">
  <span class="l">© Copyright - Paperlynx</span>
  <span class="r">PRIVACY POLICY | LICENSE AND SUBSCRIPTION TERMS</span>
</div>

</body>
</html>
```